Need Business Card for eLearning Company

Need a business card designed for our company, CareerVantly.

CareerVantly has developed a complete 12 lesson eLearning course to teach you the skills you need to present yourself in a job interview. The course uses advanced learning techniques in the multimedia videos, plus contains quizzes and additional exercises to insure you get the course and can walk into any interview with confidence and ease, and get the job.

www.careervantly-example.com

Industry/Entity Type

Business

```html
<!DOCTYPE html>
<html lang="en">
<head>
<meta charset="utf-8">
<title>CareerVantly Business Card</title>
<link rel="stylesheet" href="https://fonts.googleapis.com/css2?family=Lato:wght@300;400;700&display=swap">
<style>
  :root {
    --backdrop: #d9d6d1;
    --card-dark: #343233;
    --card-light: #ededed;
    --ink: #4a4a4a;
    --ink-soft: #6a6a6a;
    --purple: #8b2a7f;
    --green: #8dba2b;
    --white: #ffffff;
  }
  * { margin: 0; padding: 0; box-sizing: border-box; }
  html, body {
    width: 1200px; height: 900px; overflow: hidden;
    background: var(--backdrop);
    font-family: "Lato", Arial, sans-serif;
  }
  .sheet {
    width: 1200px; height: 900px;
    display: flex; flex-direction: column;
    align-items: center; justify-content: center; gap: 60px;
  }
  .card {
    width: 600px; height: 343px;
    border-radius: 4px;
    box-shadow: 0 6px 18px rgba(0,0,0,0.18);
    position: relative;
    overflow: hidden;
  }

  /* Front */
  .card--front { background: var(--card-dark); }
  .front-brand {
    position: absolute; left: 50%; top: 50%;
    transform: translate(-50%, -50%);
    display: flex; align-items: center; gap: 22px;
  }
  .brand-square {
    width: 70px; height: 70px; border-radius: 12px;
    background: var(--white);
  }
  .front-name {
    font-size: 40px; font-weight: 400; color: var(--white);
    letter-spacing: 0.5px;
  }

  /* Back */
  .card--back { background: var(--card-light); padding: 34px 40px; }
  .back-brand { display: flex; align-items: center; gap: 14px; }
  .brand-square--small {
    width: 30px; height: 30px; border-radius: 6px;
    background: var(--card-dark);
  }
  .back-name {
    font-size: 28px; font-weight: 400; color: var(--ink);
    border-bottom: 1px solid var(--ink-soft); padding-bottom: 2px;
  }
  .contact-block {
    position: absolute; left: 170px; top: 110px;
  }
  .person-name {
    font-size: 24px; font-weight: 300; color: var(--purple); line-height: 1.1;
  }
  .person-role {
    font-size: 17px; font-weight: 400; color: var(--ink);
    letter-spacing: 0.8px; text-transform: uppercase;
  }
  .contact-lines { margin-top: 30px; font-size: 14px; color: var(--ink); line-height: 1.35; }
  .contact-lines dt { float: left; width: 16px; color: var(--purple); }
  .contact-lines dd { margin-left: 16px; }
  .address { margin-top: 18px; font-size: 14px; color: var(--ink); line-height: 1.35; font-style: normal; }
  .website {
    margin-top: 18px; font-size: 15px; font-weight: 700; color: var(--purple);
  }
</style>
</head>
<body>
<main class="sheet">
  <section class="card card--front" aria-label="Card front">
    <div class="front-brand">
      <div class="brand-square"></div>
      <span class="front-name">careervantly</span>
    </div>
  </section>

  <section class="card card--back" aria-label="Card back">
    <div class="back-brand">
      <div class="brand-square--small"></div>
      <span class="back-name">careervantly</span>
    </div>
    <div class="contact-block">
      <p class="person-name">Dana Whitfield</p>
      <p class="person-role">Principal Consultant</p>
      <dl class="contact-lines">
        <dt>T</dt><dd>(555)010-4821</dd>
        <dt>E</dt><dd>support@careervantly-example.com</dd>
      </dl>
      <address class="address">420 Harbor View Lane Suite 118,<br>Lakeport, WA 98000</address>
      <p class="website">www.careervantly-example.com</p>
    </div>
  </section>
</main>
</body>
</html>
```